Business Card Design - Photographer

I am a landscape photographer and I require a business card design. 

I require two designs:
1)  a double sided business card
 and
b)  a single sided business card 

The single sided design can either be the same as the double sided (with just one side having all the information)....or it can be an entire new design. Its up to you.

My corporate colours are (CMYK):

Blue   69, 32, 0, 0
Grey  72,  64,  47,  31
Green  32,  2,  91,  0
Yellow   0, 19, 92, 0
Orange  0, 39, 75, 0

Colour space in final file should be in CMYK.

The details that need to be included on the card:

- Use the provided Logo
- Name: Wiktor Baranowski
- Email:   sales@vistalumeworks.com.au
- Website:    vistalumeworks.com.au
- Twitter:    twitter.com/vistalumeworks
- Facebook:   facebook.com/vistalumeworks
- Mobile  0417 539 662

Please use the attached template to design the logo to the specified size, including the marked bleed lines. I have also attached my logo in PNG (transparent background) and ai format for you to use.

The final file should be:
- Photoshop version with layers so I can edit the name/text etc. All non vector files should be high resolution at 1039 x 697 pixels at 300 dpi.

I also require a file as:
- Vector based PDF

Anyway questions please contact me.

Thank you

Industry/Entity Type

Landscape

Logo styles of interest
Pictorial/Combination Logo
Abstract Logo
Wordmark Logo
Lettermark Logo
Requirements
Must have
• The details that need to be included on the card:

- Use the provided Logo
- Name: Wiktor Baranowski
- Email: sales@vistalumeworks.com.au
- Website: vistalumeworks.com.au
- Twitter: twitter.com/vistalumeworks
- Facebook: facebook.com/vistalumeworks
- Mobile 0417 539 662

```html
<!DOCTYPE html>
<html lang="en">
<head>
<meta charset="utf-8">
<title>Vistalume Works – Business Cards</title>
<link href="https://fonts.googleapis.com/css2?family=Source+Sans+3:wght@400;600&display=swap" rel="stylesheet">
<style>
  :root {
    --backdrop: #a98420;
    --card-white: #ffffff;
    --ink-grey: #3a3d4c;
    --panel-dark: #23252f;
    --panel-mid: #3b3e4c;
    --brand-blue: #3d9ad6;
    --brand-green: #b3cf3a;
    --brand-yellow: #f7cd2a;
    --brand-orange: #f59f4a;
    --text-light: #ffffff;
    --icon-square: #4d6aa8;
    --icon-square-alt: #4fb3e0;
  }
  * { box-sizing: border-box; margin: 0; padding: 0; }
  html, body { width: 1200px; height: 686px; overflow: hidden; }
  body {
    background: var(--backdrop);
    font-family: "Source Sans 3", "Myriad Pro", Arial, sans-serif;
  }
  .stage { position: relative; width: 1200px; height: 686px; overflow: hidden; }

  .card {
    position: absolute;
    width: 450px;
    height: 257px;
    background: var(--card-white);
    box-shadow: 1px 2px 4px rgba(0,0,0,0.35);
    overflow: hidden;
  }
  .card--front { left: 123px; top: 189px; }
  .card--back  { left: 615px; top: 255px; }

  .card__shape { position: absolute; inset: 0; }

  .brand {
    position: absolute;
    display: flex;
    flex-direction: column;
    align-items: center;
    transform: translateX(-50%);
  }
  .brand__dot {
    border-radius: 50%;
    background: var(--ink-grey);
  }
  .brand__name {
    color: var(--ink-grey);
    font-weight: 600;
    text-transform: uppercase;
    white-space: nowrap;
    letter-spacing: 1px;
  }
  .card--front .brand { left: 119px; top: 70px; }
  .card--front .brand__dot { width: 56px; height: 56px; margin-bottom: 22px; }
  .card--front .brand__name { font-size: 19px; }

  .card--back .brand { left: 228px; top: 62px; }
  .card--back .brand__dot { width: 76px; height: 76px; margin-bottom: 28px; }
  .card--back .brand__name { font-size: 24px; letter-spacing: 1.5px; }

  .contact {
    position: absolute;
    right: 12px;
    top: 52px;
    color: var(--text-light);
    font-size: 12.5px;
    line-height: 18px;
    text-align: right;
  }
  .contact__row {
    display: flex;
    justify-content: flex-end;
    align-items: center;
    gap: 5px;
  }
  .contact__icon { width: 11px; height: 11px; flex: none; }
  .contact__social { margin-top: 9px; }
  .contact__social .contact__row { flex-direction: row; margin-right: 12px; height: 23px; }
  .contact__square { width: 15px; height: 15px; border-radius: 2px; flex: none; }
  .contact__square--fb { background: var(--icon-square); }
  .contact__square--tw { background: var(--icon-square-alt); }
  .contact__address { margin-top: 11px; margin-right: 12px; font-size: 13px; line-height: 17px; }
</style>
</head>
<body>
<main class="stage">

  <section class="card card--front" aria-label="Business card, front">
    <svg class="card__shape" width="450" height="257" viewBox="0 0 450 257" aria-hidden="true">
      <defs>
        <radialGradient id="panelGradient" cx="0.55" cy="0.35" r="0.8">
          <stop offset="0" stop-color="var(--panel-mid)"/>
          <stop offset="1" stop-color="var(--panel-dark)"/>
        </radialGradient>
        <linearGradient id="accentGradient" x1="0" y1="0" x2="0" y2="1">
          <stop offset="0.25" stop-color="var(--brand-orange)" stop-opacity="0"/>
          <stop offset="0.45" stop-color="var(--brand-orange)"/>
          <stop offset="0.62" stop-color="var(--brand-yellow)"/>
          <stop offset="0.82" stop-color="var(--brand-green)"/>
          <stop offset="1" stop-color="var(--brand-blue)"/>
        </linearGradient>
      </defs>
      <path class="card__panel" d="M172 0 Q282 112 222 257 L450 257 L450 0 Z" fill="url(#panelGradient)"/>
      <path class="card__accent" d="M163 0 Q273 112 213 257" fill="none" stroke="url(#accentGradient)" stroke-width="7"/>
    </svg>

    <div class="brand">
      <span class="brand__dot"></span>
      <span class="brand__name">Vistalume Works</span>
    </div>

    <div class="contact">
      <div class="contact__row">0417 539 662
        <svg class="contact__icon" viewBox="0 0 12 12" aria-hidden="true"><path d="M3 1 L5 3.5 L4 5 Q5 7 7 8 L8.5 7 L11 9 L9.5 11 Q5 11 1 6 Q1 3 3 1 Z" fill="#fff"/></svg>
      </div>
      <div class="contact__row">sales@vistalumeworks.com.au
        <svg class="contact__icon" viewBox="0 0 12 12" aria-hidden="true"><rect x="0.5" y="2.5" width="11" height="7.5" fill="#fff"/><path d="M0.5 2.5 L6 7 L11.5 2.5" fill="none" stroke="var(--panel-dark)" stroke-width="1"/></svg>
      </div>
      <div class="contact__row">www.vistalumeworks.com.au
        <svg class="contact__icon" viewBox="0 0 12 12" aria-hidden="true"><g fill="none" stroke="#fff" stroke-width="1"><circle cx="6" cy="6" r="5"/><ellipse cx="6" cy="6" rx="2.2" ry="5"/><path d="M1 6 H11 M2 3.3 H10 M2 8.7 H10"/></g></svg>
      </div>
      <div class="contact__social">
        <div class="contact__row"><span class="contact__square contact__square--fb"></span>@vistalumeworks</div>
        <div class="contact__row"><span class="contact__square contact__square--tw"></span>@vistalumeworks</div>
      </div>
      <div class="contact__address">Street name City<br>State, zip code</div>
    </div>
  </section>

  <section class="card card--back" aria-label="Business card, back">
    <div class="brand">
      <span class="brand__dot"></span>
      <span class="brand__name">Vistalume Works</span>
    </div>
  </section>

</main>
</body>
</html>
```